A Brochure to sell LED Downlights to clients

I am starting a campaign on google for LED down lights the link to the landing page can be found at brinholt.com.au/led .

When the client send a contact request i want to be able to send back a brochure of a picture of each light (Approx 6 - 8 types) and have a few sentences on each light and price brake down.

'Quarnel Ostrava 9w LED'

**Information**

1-10 lights $49
11-20 lights $45
21 - 40 lights $42
40 and over $40

EACH LIGHT:

Hi,

This is very good.

I
But,

Each light will have its own price.

Can i get it made like this;

Picture - Spec - Pricing in a table style please? - i like the layout it just need to suit the tables under:

picture - Brand - Price 1-10
Model - Price 11-20
Watts - Price 21-21
lumen - price 30- 40
Warranty = price 40+

Model - Price 11-20
Watts - Price 21-21
lumen - price 30- 40
Warranty = price 40+

Model - Price 11-20
Watts - Price 21-21
lumen - price 30- 40
Warranty = price 40+

and so on....

I want it to be on Microsoft Word so i can easily chop and edit the prices and images also. (So i can print to PDF)

For more information see my website to seek inspiration. I have a zip file of my logo for actual creation and should be also to source pictures of the lights when finalising the design.

brinholt.com.au

Thanks

Added 2 x additional Dimmers please see zip file, same layout/pricing as the downlights

Target Market(s)

Homeowners/commercial business owners

Industry/Entity Type

Electric Company

Font styles to use
Sans Serif

Colors
86cfc6
ffffff
000000

Requirements
Must have
• Professional looking, Colours to the theme of my logo/website
Nice to have
• An awesome design that sells it's self!!!!!!!
• My Logo font is 'Radikil" it would be nice to follow that theme if it doesn't look good i am open to have a nice legible font for the copy.
Should not have
• Cheesy light globes or images

```html
<!DOCTYPE html>
<html lang="en">
<head>
<meta charset="utf-8">
<title>Brinholt Electrical – LED Downlight Catalog</title>
<link rel="stylesheet" href="https://fonts.googleapis.com/css2?family=Montserrat:wght@700&family=Questrial&display=swap">
<style>
  :root {
    --canvas: #c9c9c9;
    --teal: #17a99a;
    --teal-soft: #86cfc6;
    --charcoal: #3e3e3e;
    --ink: #222222;
    --paper: #ffffff;
    --paper-grey: #f1f2f2;
    --rule: #8a8a8a;
  }
  * { box-sizing: border-box; margin: 0; padding: 0; }
  html, body { width: 1200px; height: 2980px; overflow: hidden; }
  body {
    background: var(--canvas);
    font-family: "Questrial", "Century Gothic", sans-serif;
    color: var(--ink);
    position: relative;
  }
  .page {
    position: absolute;
    left: 290px;
    width: 622px;
    height: 880px;
    overflow: hidden;
    box-shadow: 6px 8px 12px rgba(0,0,0,0.35);
  }
  .page--cover { top: 115px; background: var(--paper); }
  .page--range { top: 1069px; background: linear-gradient(180deg, var(--paper-grey), #e6e8e8 60%, var(--paper) 100%); }
  .page--back  { top: 2023px; background: var(--teal); }

  /* Cover */
  .cover-title {
    position: absolute; top: 44px; left: 0; width: 100%;
    text-align: center;
    font-family: "Montserrat", sans-serif; font-weight: 700;
    font-size: 62px; letter-spacing: 3px; line-height: 1;
    color: var(--teal);
  }
  .cover-subtitle {
    position: absolute; top: 112px; left: 158px; width: 306px; height: 64px;
    border: 2px solid var(--rule);
    text-align: center;
    font-size: 54px; line-height: 60px; letter-spacing: 2px;
    color: var(--charcoal);
  }
  .cover-photo {
    position: absolute; top: 180px; left: 0; width: 100%; height: 514px;
    background: linear-gradient(180deg, #ffffff 0%, #f2efe9 25%, #e4ddd2 55%, #cfc6b8 78%, #8c8479 100%);
  }
  .cover-band { position: absolute; top: 694px; left: 0; width: 100%; height: 12px; background: var(--teal); }
  .cover-footer { position: absolute; top: 706px; left: 0; width: 100%; height: 174px; background: var(--charcoal); }
  .brand {
    display: flex; align-items: center; gap: 12px;
    color: var(--paper); font-size: 34px; line-height: 1;
  }
  .brand-mark { width: 26px; height: 26px; background: var(--teal); flex: none; }
  .cover-footer .brand { position: absolute; left: 22px; top: 86px; }
  .cover-url {
    position: absolute; right: 26px; bottom: 20px;
    color: var(--paper); font-size: 22px;
  }

  /* Range page */
  .range-heading {
    position: absolute; top: 34px; left: 0; width: 100%;
    text-align: center;
    font-family: "Montserrat", sans-serif; font-weight: 700;
    font-size: 24px; color: var(--teal); letter-spacing: 0.5px;
  }
  .product {
    position: absolute; left: 88px; width: 516px; height: 144px;
    background: var(--paper);
    border: 2px solid var(--teal);
    border-radius: 24px;
  }
  .product:nth-of-type(1) { top: 76px; }
  .product:nth-of-type(2) { top: 236px; }
  .product:nth-of-type(3) { top: 396px; }
  .product:nth-of-type(4) { top: 556px; }
  .product-photo {
    position: absolute; left: -72px; top: 10px; width: 118px; height: 118px;
    border-radius: 50%;
    background: radial-gradient(circle at 45% 40%, #ffffff 0%, #e2e4e4 45%, #9a9d9e 80%, #5d6062 100%);
  }
  .product-name {
    position: absolute; left: 60px; top: 12px;
    font-size: 21px; font-weight: 400; color: var(--teal);
    border-bottom: 2px solid var(--teal-soft); padding-bottom: 1px;
  }
  .product-specs {
    position: absolute; left: 60px; top: 48px; width: 446px;
    list-style: none;
    display: grid; grid-template-columns: 214px 222px; column-gap: 10px; row-gap: 6px;
    font-size: 12px; line-height: 15px; color: #333;
  }
  .product-specs li { position: relative; padding-left: 20px; white-space: nowrap; }
  .product-specs li::before {
    content: ""; position: absolute; left: 0; top: 1px;
    width: 12px; height: 12px; border-radius: 50%; background: var(--teal);
  }
  .product-prices {
    position: absolute; left: 60px; right: 14px; bottom: 10px;
    display: flex; justify-content: space-between;
    border-top: 1px solid var(--teal-soft); padding-top: 5px;
    font-size: 12px; color: #333; white-space: nowrap;
  }
  .product-prices .amount { color: var(--teal); }
  .price-label {
    position: absolute; top: 716px; left: 214px; width: 282px; height: 28px;
    background: var(--teal); color: var(--paper);
    text-align: center; font-size: 18px; line-height: 28px;
  }
  .price-table {
    position: absolute; top: 744px; left: 28px; width: 576px; height: 90px;
    background: var(--charcoal);
    border: 3px solid var(--teal);
    border-radius: 18px;
    display: grid; grid-template-columns: 1fr 1fr; align-content: center;
    padding: 0 36px; row-gap: 4px;
    color: var(--paper); font-size: 21px;
  }
  .price-table .amount { color: var(--teal); }
  .range-url { position: absolute; right: 26px; top: 846px; font-size: 15px; color: #444; }

  /* Back */
  .back-strip { position: absolute; top: 0; left: 0; width: 100%; height: 12px; background: #7b7b7b; }
  .back-photo {
    position: absolute; top: 12px; left: 0; width: 100%; height: 868px;
    background: radial-gradient(ellipse at 50% 80%, rgba(0,70,62,0.35) 0%, rgba(0,70,62,0) 60%),
                linear-gradient(180deg, #16a596 0%, #1aa99b 45%, #12998b 100%);
  }
  .page--back .brand {
    position: absolute; top: 322px; left: 0; width: 100%;
    justify-content: center; font-size: 36px;
  }
  .page--back .brand-mark { background: var(--paper); }
  .back-url {
    position: absolute; bottom: 22px; left: 0; width: 100%;
    text-align: center; color: var(--paper); font-size: 22px; letter-spacing: 0.5px;
  }
</style>
</head>
<body>

<section class="page page--cover">
  <h1 class="cover-title">PRODUCT</h1>
  <div class="cover-subtitle">CATALOG</div>
  <div class="cover-photo" role="img" aria-label="Retail shop interior lit by recessed LED downlights, with shelves of shoes and a bicycle in the window"></div>
  <div class="cover-band"></div>
  <div class="cover-footer">
    <div class="brand"><span class="brand-mark"></span><span>Brinholt Electrical</span></div>
    <div class="cover-url">brinholt.com.au</div>
  </div>
</section>

<section class="page page--range">
  <h2 class="range-heading">CHOOSE YOUR STYLE OF LED DOWNLIGHTS</h2>

  <article class="product">
    <div class="product-photo" role="img" aria-label="White round LED downlight"></div>
    <h3 class="product-name">Quarnel Ostrava 9w LED</h3>
    <ul class="product-specs">
      <li>Save 80% on your energy bills</li>
      <li>Up to 7 years manufacturer's warranty</li>
      <li>50,000 hours of life</li>
      <li>Brighter than halogen downlights</li>
    </ul>
    <div class="product-prices">
      <span>1-10: <span class="amount">$49</span></span>
      <span>11-20: <span class="amount">$45</span></span>
      <span>21-40: <span class="amount">$42</span></span>
      <span>40+: <span class="amount">$40</span></span>
    </div>
  </article>

  <article class="product">
    <div class="product-photo" role="img" aria-label="White LED downlight with driver cable"></div>
    <h3 class="product-name">Quarnel Tarvo 10w LED</h3>
    <ul class="product-specs">
      <li>Save 80% on your energy bills</li>
      <li>Up to 7 years manufacturer's warranty</li>
      <li>50,000 hours of life</li>
      <li>Brighter than halogen downlights</li>
    </ul>
    <div class="product-prices">
      <span>1-10: <span class="amount">$52</span></span>
      <span>11-20: <span class="amount">$48</span></span>
      <span>21-40: <span class="amount">$45</span></span>
      <span>40+: <span class="amount">$43</span></span>
    </div>
  </article>

  <article class="product">
    <div class="product-photo" role="img" aria-label="Dark gimbal LED downlight with driver"></div>
    <h3 class="product-name">Quarnel Lisen 12w LED</h3>
    <ul class="product-specs">
      <li>Save 80% on your energy bills</li>
      <li>Up to 7 years manufacturer's warranty</li>
      <li>50,000 hours of life</li>
      <li>Brighter than halogen downlights</li>
    </ul>
    <div class="product-prices">
      <span>1-10: <span class="amount">$55</span></span>
      <span>11-20: <span class="amount">$51</span></span>
      <span>21-40: <span class="amount">$48</span></span>
      <span>40+: <span class="amount">$46</span></span>
    </div>
  </article>

  <article class="product">
    <div class="product-photo" role="img" aria-label="Brushed chrome LED downlight with heat sink"></div>
    <h3 class="product-name">Quarnel Merrow 13w LED</h3>
    <ul class="product-specs">
      <li>Save 80% on your energy bills</li>
      <li>Up to 7 years manufacturer's warranty</li>
      <li>50,000 hours of life</li>
      <li>Brighter than halogen downlights</li>
    </ul>
    <div class="product-prices">
      <span>1-10: <span class="amount">$59</span></span>
      <span>11-20: <span class="amount">$55</span></span>
      <span>21-40: <span class="amount">$52</span></span>
      <span>40+: <span class="amount">$50</span></span>
    </div>
  </article>

  <div class="price-label">Quarnel Ostrava 9w LED</div>
  <div class="price-table">
    <div>1-10.......lights : <span class="amount">$49</span></div>
    <div>21-40...lights : <span class="amount">$42</span></div>
    <div>11-20...lights : <span class="amount">$45</span></div>
    <div>40 and over : <span class="amount">$40</span></div>
  </div>
  <div class="range-url">www.brinholt.com.au</div>
</section>

<section class="page page--back">
  <div class="back-photo" role="img" aria-label="Dim bedroom interior with ceiling downlights, tinted teal"></div>
  <div class="back-strip"></div>
  <div class="brand"><span class="brand-mark"></span><span>Brinholt Electrical</span></div>
  <div class="back-url">www.brinholt.com.au</div>
</section>

</body>
</html>
```